Website Design for a Chemical Sales Company

We are working with a Chemical Sales Company in California. They sell various chemicals throughout the US.
Types of products they sell: https://www.wardenvale.example/us/products/all
https://www.molvista.example/products/kerrin/glacyn-glycol-thermal-fluids/glacyn-propylene-glycol-thermal-fluids
Some sites to use for inspiration:
https://www.molvista.example
https://www.kerrin.example/en-us
Thank you for taking the time to consider designing a website for us. We are web developers based in Stockton, CA, USA. Most of our projects go through the same process. Understanding this process may help you win a project with us. We custom-code all of our websites in-house. We don’t have any requirements as to what tools you use for your design, but we ask that you follow these guidelines.
IMAGES:
If you use any images or icons in the design, we ask that you have a link to the asset so we can purchase the image/icon. Most of the designs we submit do not have the customer’s images on them unless they have some great images. Be creative; show us the feeling you are trying to portray with your image choices. Use any royalty-free site you choose. We subscribe to Pelmora and mainly use their images, but we can purchase images outside of Pelmora. PLEASE NOTE: we will not submit designs to clients with watermarks on the images.
FONTS:
We ask that you identify the fonts you’re using in the design. This can be done in a message if you want. We typically use Google Fonts and Pelmora Fonts.
CONTENT:
We're always open to different content and ideas. We often submit designs with stock images so the client can see our vision. We typically take pictures after the website launch to use their images with our vision. Lorem Ipsum is fine for paragraphs, but we ask that you make the Headers with correct English. We want to be able to show the vision and identify the sections of the website.
INSPIRATION:
We typically add a couple of links in the brief of websites we like to help you get started in your design.
REVISIONS:
We do not often ask for revisions of the designs unless we see something in the design that may not appeal to the client. If there are slight changes that we want to make, we do that in the development process.
FEEDBACK:
We rarely give feedback on designs during the design process. We are working on many website projects and do not have the time to provide feedback. We usually respond if your request is well thought out and asks specific questions, but a note asking “feedback, please” usually goes unanswered.

```html
<!DOCTYPE html>
<html lang="en">
<head>
<meta charset="utf-8">
<title>Velantra Chem</title>
<link href="https://fonts.googleapis.com/css2?family=Poppins:wght@300;400;500;600&display=swap" rel="stylesheet">
<style>
:root{
  --blue:#0b8fd9;
  --blue-bright:#1ba3e8;
  --navy:#0f2a44;
  --ink:#111;
  --muted:#444;
  --gray-bg:#f6f6f6;
  --field:#f2f2f2;
  --star:#f5a623;
  --black:#000;
  --white:#fff;
}
*{box-sizing:border-box;margin:0;padding:0}
html,body{width:1200px;height:3791px;overflow:hidden}
body{position:relative;font-family:'Poppins',sans-serif;color:var(--ink);background:var(--white)}
.abs{position:absolute}
.center{text-align:center}

/* hero */
.hero{left:0;top:0;width:1200px;height:672px;background:radial-gradient(ellipse at 50% 55%,#4c6f8f 0%,#24466a 40%,#0e2540 80%,#081a30 100%)}
.menu{left:112px;top:34px;color:var(--white);font-size:18px;display:flex;align-items:center;gap:14px}
.brand-top{left:0;width:1200px;top:58px;color:var(--white);font-size:30px;font-weight:300;letter-spacing:3px;display:flex;justify-content:center;align-items:center;gap:10px}
.dot{width:14px;height:14px;border-radius:50%;background:var(--blue-bright);display:inline-block}
.login{left:967px;top:28px;width:120px;height:50px;background:var(--blue);color:var(--white);border-radius:0 14px 0 14px;font-size:17px;display:flex;align-items:center;justify-content:center}
.hero-welcome{left:0;width:1200px;top:252px;color:var(--white);font-size:56px;font-weight:300;letter-spacing:1px}
.hero-name{left:0;width:1200px;top:320px;color:var(--white);font-size:86px;font-weight:300;letter-spacing:3px}

/* products */
.section-title{left:0;width:1200px;font-size:35px;font-weight:400;color:var(--ink)}
.product-art{border-radius:2px}
.card-box{left:448px;top:858px;width:291px;height:293px;background:var(--white);box-shadow:0 4px 20px rgba(0,0,0,.1)}
.p-title{width:300px;font-size:20px;letter-spacing:.5px}
.stars{width:300px;color:var(--star);font-size:17px;letter-spacing:5px}
.btn-cart{width:152px;height:44px;border-radius:22px;background:var(--blue-bright);color:var(--white);font-size:15px;display:flex;align-items:center;justify-content:center}
.arrow{width:18px;height:18px;border-radius:50%;display:flex;align-items:center;justify-content:center;font-size:10px}

/* about */
.about-band{left:368px;top:1433px;width:832px;height:500px;background:linear-gradient(120deg,#1a8fd6 0%,#0f78c2 60%,#2390d0 100%)}
.about-photo{left:33px;top:1420px;width:522px;height:522px;border-radius:50%;background:radial-gradient(circle at 45% 45%,#d8ecf4 0%,#8cc6de 40%,#3b93bd 75%,#1d6a97 100%);box-shadow:0 0 0 2px rgba(255,255,255,.3)}
.about-title{left:595px;top:1493px;color:var(--white);font-size:37px;font-weight:300}
.about-text{left:595px;top:1548px;width:545px;color:var(--white);font-size:16px;line-height:30px;font-weight:300}
.btn-read{left:595px;top:1814px;width:153px;height:50px;background:var(--white);color:var(--blue);border-radius:0 16px 0 16px;font-size:16px;display:flex;align-items:center;justify-content:center}

/* testimonials */
.testi-bg{left:0;top:2027px;width:1200px;height:625px;background:var(--gray-bg)}
.testi-card{left:239px;top:2210px;width:715px;height:312px;background:var(--white);box-shadow:0 4px 20px rgba(0,0,0,.06)}
.quote{left:569px;top:2181px;width:58px;height:58px;border-radius:50%;background:var(--blue);color:var(--white);font-size:38px;font-weight:600;display:flex;align-items:center;justify-content:center;line-height:1}
.t-name{font-size:19px}
.t-text{font-size:14.5px;line-height:30px;color:var(--muted)}
.ghost{color:#aaa}
.progress{left:289px;top:2563px;width:633px;height:4px;background:#ddd}
.progress span{position:absolute;left:226px;top:0;width:180px;height:4px;background:var(--blue-bright)}

/* contact */
.footer-bg{left:0;top:3182px;width:1200px;height:609px;background:var(--black)}
.contact-card{left:97px;top:2740px;width:1004px;height:544px;background:var(--white);border-radius:16px;box-shadow:0 4px 30px rgba(0,0,0,.08)}
.c-text{font-size:15px;line-height:34px;color:var(--muted)}
.field{background:var(--field);border-radius:25px;font-size:13px;color:#777;padding-left:25px;display:flex;align-items:center;justify-content:space-between;padding-right:30px}
.msg{align-items:flex-start;padding-top:20px;border-radius:25px}
.btn-send{left:505px;top:3183px;width:189px;height:50px;background:var(--blue);color:var(--white);border-radius:4px;font-size:13px;font-weight:600;display:flex;align-items:center;justify-content:center}

/* footer */
.f-brand{left:115px;top:3480px;color:var(--white);font-size:44px;font-weight:300;letter-spacing:2px;display:flex;align-items:center;gap:12px}
.f-brand .dot{width:20px;height:20px}
.f-title{color:var(--white);font-size:23px}
.news-input{left:515px;top:3481px;width:277px;height:35px;border:1px solid #777;color:#aaa;font-size:11px;padding-left:14px;display:flex;align-items:center}
.news-btn{left:792px;top:3481px;width:111px;height:35px;background:var(--blue);color:var(--white);font-size:10px;font-weight:600;display:flex;align-items:center;justify-content:center}
.f-label{color:var(--white);font-size:15px}
.f-item{color:var(--white);font-size:12.5px;line-height:20px;display:flex;gap:10px}
.f-line{left:115px;top:3690px;width:970px;height:1px;background:#333}
.copy{left:135px;top:3726px;color:var(--white);font-size:13.5px}
.social{left:1034px;top:3723px;width:28px;height:28px;border:2px solid var(--blue);border-radius:50%}
</style>
</head>
<body>

<!-- HERO -->
<div class="abs hero" role="img" aria-label="Blue macro photograph of water droplets and bubbles on a molecular strand"></div>
<div class="abs menu">
  <svg width="20" height="16" viewBox="0 0 20 16"><rect y="0" width="16" height="2.4" fill="#fff"/><rect y="6.8" width="20" height="2.4" fill="#fff"/><rect y="13.6" width="12" height="2.4" fill="#fff"/></svg>
  <span>Menu</span>
</div>
<div class="abs brand-top"><span class="dot"></span><span>VELANTRA CHEM</span></div>
<div class="abs login">Login</div>
<div class="abs hero-welcome center">WELCOME TO</div>
<div class="abs hero-name center">VELANTRA CHEM</div>

<!-- BEST PRODUCTS -->
<div class="abs section-title center" style="top:764px">BEST PRODUCTS</div>

<div class="abs arrow" style="left:50px;top:1045px;background:#eee;color:#999">‹</div>
<div class="abs arrow" style="left:1131px;top:1047px;background:var(--blue);color:#fff">›</div>

<div class="abs product-art" style="left:188px;top:900px;width:140px;height:200px;background:linear-gradient(180deg,#d8d8d8,#3a3a3a 50%,#1d1d1d)" role="img" aria-label="Black magnetic filter unit with brass valves"></div>

<div class="abs card-box"></div>
<div class="abs product-art" style="left:533px;top:900px;width:120px;height:210px;border-radius:40px 40px 30px 30px;background:linear-gradient(180deg,#e53b20,#c9260f)" role="img" aria-label="Red portable power flushing pump"></div>

<div class="abs product-art" style="left:862px;top:920px;width:135px;height:180px;border-radius:12px;background:linear-gradient(180deg,#3fc7c9,#e6f7f8 45%,#d0eef0)" role="img" aria-label="White and teal container of system cleaning chemical"></div>

<div class="abs p-title center" style="left:109px;top:1187px">CLEARSTREAM CYCLONE</div>
<div class="abs p-title center" style="left:443px;top:1187px">PURGEFLOW P90</div>
<div class="abs p-title center" style="left:778px;top:1187px">PURGEFLOW TEST KIT</div>

<div class="abs stars center" style="left:105px;top:1228px">★★★★★</div>
<div class="abs stars center" style="left:440px;top:1224px">★★★★★</div>
<div class="abs stars center" style="left:774px;top:1228px">★★★★★</div>

<div class="abs btn-cart" style="left:178px;top:1271px">Add To Cart</div>
<div class="abs btn-cart" style="left:512px;top:1267px">Add To Cart</div>
<div class="abs btn-cart" style="left:847px;top:1271px">Add To Cart</div>

<!-- ABOUT -->
<div class="abs about-band" role="img" aria-label="Blue background with faint molecular structure imagery"></div>
<div class="abs about-photo" role="img" aria-label="Scientist in protective suit working at a laboratory microscope"></div>
<div class="abs about-title">ABOUT US</div>
<p class="abs about-text">Lorem ipsum dolor sit amet, consectetur adipiscing elit, sed do eiusmod tempor incididunt ut labore et dolore magna aliqua. Quis ipsum suspendisse ultrices gravida. Risus commodo viverra maecenas accumsan lacus vel facilisis. Lorem ipsum dolor sit amet, consectetur adipiscing elit, sed do eiusmod tempor incididunt ut labore et dolore magna aliqua. Quis ipsum suspendisse ultrices gravida. Risus commodo viverra maecenas accumsan lacus vel facilisis. Lorem ipsum dolor sit amet, consectetur adipiscing elit,</p>
<div class="abs btn-read">Read More</div>

<!-- TESTIMONIALS -->
<div class="abs testi-bg"></div>
<div class="abs section-title center" style="top:2097px">CLIENT TESTIMONIALS</div>

<div class="abs t-name ghost" style="left:-10px;top:2284px">nnett</div>
<div class="abs t-text ghost" style="left:-10px;top:2328px;width:220px;text-align:right">eiusmod tempor incididunt ut<br>ravida. Risus commodo viver-<br>et, consectetur</div>
<div class="abs t-name ghost" style="left:1148px;top:2284px">Marlo</div>
<div class="abs t-text ghost" style="left:990px;top:2328px;width:240px;text-align:center">Lorem ipsum dolor sit amet, c<br>labore et dolore magna aliqua.<br>ra maecenas ac</div>

<div class="abs testi-card"></div>
<div class="abs quote">“</div>
<div class="abs stars center" style="left:446px;top:2250px;width:300px">★★★★★</div>
<div class="abs t-name center" style="left:239px;top:2284px;width:715px">MARLOW BENNETT</div>
<p class="abs t-text center" style="left:260px;top:2328px;width:675px">Lorem ipsum dolor sit amet, consectetur adipiscing elit, sed do eiusmod tempor incididunt ut labore et dolore magna aliqua. Quis ipsum suspendisse ultrices gravida. Risus commodo viverra maecenas accumsan Lorem ipsum dolor sit amet, consectetur</p>
<div class="abs center" style="left:239px;top:2436px;width:715px;font-size:21px">THANKS FAIRY DOGMOTHER</div>
<div class="abs center" style="left:239px;top:2476px;width:700px;font-size:14.5px;color:var(--muted)">Oct 04,2023</div>
<div class="abs progress"><span></span></div>

<!-- CONTACT -->
<div class="abs footer-bg"></div>
<div class="abs contact-card"></div>
<div class="abs section-title center" style="top:2792px">CONTACT US</div>
<p class="abs c-text center" style="left:200px;top:2841px;width:800px">Lorem ipsum dolor sit amet, consectetur adipiscing elit, sed do eiusmod tempor incididunt ut labore et dolore magna aliqua. Quis ipsum suspendisse ultrices gravida.ilisis.</p>

<div class="abs field" style="left:134px;top:2943px;width:453px;height:50px"><span>Name</span>
  <svg width="12" height="13" viewBox="0 0 12 13"><circle cx="6" cy="3.5" r="3" fill="#666"/><path d="M0 13c0-4 2.5-6 6-6s6 2 6 6z" fill="#666"/></svg></div>
<div class="abs field" style="left:601px;top:2943px;width:459px;height:50px"><span>Email</span>
  <svg width="14" height="10" viewBox="0 0 14 10"><rect width="14" height="10" fill="#666"/><path d="M0 0l7 5 7-5" stroke="#f2f2f2" fill="none"/></svg></div>
<div class="abs field msg" style="left:134px;top:3018px;width:929px;height:133px"><span>Message</span></div>
<div class="abs btn-send">SEND MESSAGE</div>

<!-- FOOTER -->
<div class="abs f-brand"><span class="dot"></span><span>VELANTRA CHEM</span></div>
<div class="abs f-title" style="left:515px;top:3428px">OUR NEWSLETTER</div>
<div class="abs news-input">Email Address</div>
<div class="abs news-btn">SUBSCRIBE</div>
<div class="abs f-label" style="left:515px;top:3557px">CONTACT US</div>

<div class="abs f-item" style="left:514px;top:3595px">
  <svg width="14" height="18" viewBox="0 0 14 18"><path d="M7 0a7 7 0 0 0-7 7c0 5 7 11 7 11s7-6 7-11a7 7 0 0 0-7-7z" fill="#1ba3e8"/><circle cx="7" cy="7" r="2.6" fill="#000"/></svg>
  <span>48 Harlow Row Lorem<br>ipsum dolor sit amet</span></div>
<div class="abs f-item" style="left:746px;top:3595px">
  <svg width="16" height="16" viewBox="0 0 16 16" style="margin-top:6px"><path d="M3 1l3 3-2 2c1 2 3 4 6 6l2-2 3 3-2 2C7 15 1 9 1 3z" fill="#1ba3e8"/></svg>
  <span>Phone<br>+1 555 014 2270</span></div>
<div class="abs f-item" style="left:886px;top:3595px">
  <svg width="16" height="14" viewBox="0 0 16 14" style="margin-top:6px"><path d="M1 6l7-5 7 5v7H1z M1 6l7 5 7-5" stroke="#1ba3e8" stroke-width="1.5" fill="none"/></svg>
  <span>Email<br>hello@velantrachem.example</span></div>

<div class="abs f-line"></div>
<div class="abs copy">© 2023 Velantra Chem All rights reserved. Terms And Conditions</div>
<div class="abs social" aria-label="Social profile link"></div>

</body>
</html>
```